Infographic for a Christian church discipleship pathway

We need to take a fairly complex program that helps people in a Baptist church follow Jesus, and turn it into a simple graphic. This graphic does not have to explain the whole program, web pages and print materials will do that. But, it should be something that people see and understand what it is quickly. The attached graphic is only to give the key words and general direction of the program. It should not serve as a design guide. In other words, we want to see some other ideas how this information can be imparted graphically with concision and creativity. It's important to note, the categories at the top (pray daily, read daily, gather weekly) are first steps, starting points....one shouldn't move forward until they've incorporated these things into their life. However, the categories that follow (study, connect, serve, etc) are not necessarily steps to take in sequential order.

The diagrams we've provided are not what we expect. They are only to explain the program. Here is a verbal description: The motto of our church is "A Ready Church" (ready to serve, ready to love, ready for when Jesus returns). There are four words that describe a ready church member: FOCUSED on the return of Christ, FAITHFUL in a daily relationship with Jesus, PREPARED for any opportunity to be a supernatural vessel of God's worK, LOOKING to invite others into God's family. The first two are God's Work in Me (Focused and faithful); the second two are God's Work Through me (Prepared, looking). Please use those two things as you wish (Focused faithful prepared looking; and God's word in and through me). If they are clarifying, please use. If not, you don't have to use.

Additionally, the strategies we employ to be "a ready church" are 1. Prayer 2. God's Word, and 3. Biblical Community. (So, in other words, these three things help us be a people who is focused, faithful, prepared, and looking....which is a ready church.

To provide some information how we will build this out: this graphic will be used in print and digital content. The digital content will allow people to click on each category to access training and resources associated with that discipline. (Fasting, reflecting, etc).

www.kvt.church

Target Market(s)

35-50

Industry/Entity Type

Religious

Other font styles liked:
• Lato and/or Cambria

Requirements
Must have
• Fonts: lato, cambria. Colors#: 373E41, ebebe8, #a69677. Accent Colors: 80401D, #4e5730, #a5bac8
Nice to have
• A designer who has an understanding of what it means to incorporate the spiritual disciplines of the Christian faith into their life.

```html
<!DOCTYPE html>
<html lang="en">
<head>
<meta charset="utf-8">
<title>A Ready Church – Rhythms &amp; Practices for a Ready Life</title>
<link rel="stylesheet" href="https://fonts.googleapis.com/css2?family=Lora:wght@700&family=Poppins:wght@400;600;700;800&display=swap">
<style>
  :root {
    --ink: #373e41;
    --paper: #ebebe8;
    --tan: #a69677;
    --rust: #80401d;
    --olive: #4e5730;
    --sky: #a5bac8;
    --navy: #1f527a;
    --link: #1c4e6e;
    --white: #ffffff;
  }
  html, body {
    margin: 0;
    padding: 0;
    width: 1200px;
    height: 967px;
    overflow: hidden;
    background: var(--white);
  }
  .poster { display: block; width: 1200px; height: 967px; }
  .brand-name { font-family: "Lora", Cambria, serif; font-weight: 700; font-size: 30px; fill: var(--ink); }
  .brand-mark { fill: none; stroke: var(--ink); stroke-width: 3; }
  .title { font-family: "Lora", Cambria, serif; font-weight: 700; font-size: 78px; fill: var(--tan); }
  .subtitle-band { fill: var(--ink); }
  .subtitle { font-family: "Poppins", Lato, sans-serif; font-weight: 700; font-size: 22px; letter-spacing: 4px; fill: var(--white); }
  .pillar-band, .pillar-post { fill: var(--tan); }
  .badge { fill: var(--ink); stroke: var(--white); stroke-width: 2; }
  .badge-glyph { fill: none; stroke: var(--tan); stroke-width: 2.5; stroke-linecap: round; stroke-linejoin: round; }
  .quality { font-family: "Poppins", Lato, sans-serif; font-weight: 800; font-size: 34px; fill: var(--navy); }
  .direction { font-family: "Poppins", Lato, sans-serif; font-weight: 400; font-size: 27px; fill: var(--white); }
  .post-mark { fill: none; stroke: var(--ink); stroke-width: 3; }
  .strategy-head { font-family: "Poppins", Lato, sans-serif; font-weight: 700; font-size: 17px; fill: var(--ink); text-anchor: middle; }
  .strategy-body { font-family: "Poppins", Lato, sans-serif; font-weight: 400; font-size: 13px; fill: var(--white); text-anchor: middle; }
  .strategy-rule { stroke: var(--ink); stroke-width: 2; }
  .link { fill: none; stroke: var(--link); stroke-width: 2.5; }
  .link-dot { fill: var(--link); }
  .practice-rust { fill: var(--rust); }
  .practice-olive { fill: var(--olive); }
  .practice-label { font-family: "Poppins", Lato, sans-serif; font-weight: 700; font-size: 14px; fill: var(--white); text-anchor: middle; }
</style>
</head>
<body>
<svg class="poster" viewBox="0 0 1200 967" xmlns="http://www.w3.org/2000/svg">
  <defs>
    <linearGradient id="sky-wash" x1="1" y1="0" x2="0" y2="1">
      <stop offset="0" stop-color="#b3d8e3"/>
      <stop offset="0.45" stop-color="#e4eef2"/>
      <stop offset="0.8" stop-color="#f7f6f4"/>
      <stop offset="1" stop-color="#fbeee4"/>
    </linearGradient>
    <path id="chevron" d="M0 0 H118 L151 42.5 L118 85 H0 L32 42.5 Z"/>
    <g id="pair-link">
      <path class="link" d="M0 20 V0 H197 V20"/>
      <circle class="link-dot" cx="0" cy="20" r="4"/>
      <circle class="link-dot" cx="197" cy="20" r="4"/>
      <path class="link" d="M0 113 V137 H197 V113"/>
      <circle class="link-dot" cx="0" cy="113" r="4"/>
      <circle class="link-dot" cx="197" cy="113" r="4"/>
    </g>
  </defs>

  <rect x="0" y="0" width="1200" height="967" fill="url(#sky-wash)" role="img" aria-label="Soft sky photograph with a faint cross in the background"/>

  <!-- Brand -->
  <g class="brand">
    <rect class="brand-mark" x="44" y="75" width="70" height="94"/>
    <text class="brand-name" x="127" y="105">KESTREL</text>
    <text class="brand-name" x="127" y="137">VALLEY</text>
    <text class="brand-name" x="127" y="168">TABERNACLE</text>
  </g>

  <!-- Heading -->
  <text class="title" x="386" y="111" textLength="748" lengthAdjust="spacingAndGlyphs">A READY CHURCH</text>
  <rect class="subtitle-band" x="380" y="125" width="750" height="52" rx="5"/>
  <text class="subtitle" x="755" y="160" text-anchor="middle" textLength="712" lengthAdjust="spacing">RHYTHMS &amp; PRACTICES FOR A READY LIFE</text>

  <!-- Crossbeam: four qualities -->
  <rect class="pillar-band" x="73" y="259" width="1027" height="108" rx="3"/>
  <rect class="pillar-post" x="539" y="204" width="135" height="745" rx="4"/>

  <g class="badge-focused">
    <circle class="badge" cx="175" cy="248" r="28"/>
    <circle class="badge-glyph" cx="175" cy="248" r="16"/>
    <circle class="badge-glyph" cx="175" cy="248" r="9"/>
    <circle class="badge-glyph" cx="175" cy="248" r="2.5"/>
  </g>
  <g class="badge-faithful">
    <circle class="badge" cx="421" cy="248" r="28"/>
    <path class="badge-glyph" d="M409 262 L418 236 L421 250 L424 236 L433 262"/>
  </g>
  <g class="badge-prepared">
    <circle class="badge" cx="792" cy="248" r="28"/>
    <path class="badge-glyph" d="M792 231 V266 M779 243 H805" stroke-width="5"/>
  </g>
  <g class="badge-looking">
    <circle class="badge" cx="998" cy="248" r="28"/>
    <path class="badge-glyph" d="M979 248 Q998 230 1017 248 Q998 266 979 248 Z"/>
    <circle class="badge-glyph" cx="998" cy="248" r="5"/>
  </g>

  <text class="quality" x="102" y="317">FOCUSED</text>
  <text class="quality" x="340" y="317">FAITHFUL</text>
  <text class="quality" x="710" y="317">PREPARED</text>
  <text class="quality" x="930" y="317">LOOKING</text>
  <text class="direction" x="100" y="353">God's Work In Me</text>
  <text class="direction" x="710" y="353">God's Work Through Me</text>

  <!-- Post: three strategies -->
  <rect class="post-mark" x="566" y="262" width="80" height="96"/>

  <text class="strategy-head" x="606" y="427">PRAYER</text>
  <text class="strategy-body" x="606" y="456">Become a</text>
  <text class="strategy-body" x="606" y="473">person devoted</text>
  <text class="strategy-body" x="606" y="490">to prayer each</text>
  <text class="strategy-body" x="606" y="507">day of your life.</text>
  <line class="strategy-rule" x1="551" y1="537" x2="664" y2="537"/>

  <text class="strategy-head" x="606" y="590">GOD'S</text>
  <text class="strategy-head" x="606" y="609">WORD</text>
  <text class="strategy-body" x="606" y="637">Build a daily</text>
  <text class="strategy-body" x="606" y="654">habit of</text>
  <text class="strategy-body" x="606" y="671">beholding God</text>
  <text class="strategy-body" x="606" y="688">in His Word.</text>
  <line class="strategy-rule" x1="551" y1="713" x2="664" y2="713"/>

  <text class="strategy-head" x="606" y="784">BIBLICAL</text>
  <text class="strategy-head" x="606" y="802">COMMUNITY</text>
  <text class="strategy-body" x="606" y="835">Engage deeply</text>
  <text class="strategy-body" x="606" y="852">in Christian</text>
  <text class="strategy-body" x="606" y="869">community.</text>
  <line class="strategy-rule" x1="551" y1="888" x2="664" y2="888"/>

  <!-- Practices: God's work in me -->
  <g class="practice-group" transform="translate(0,0)">
    <use href="#pair-link" x="191" y="406"/>
    <use href="#chevron" class="practice-rust" x="115" y="430"/>
    <text class="practice-label" x="190" y="495">REST</text>
    <use href="#chevron" class="practice-olive" x="319" y="430"/>
    <text class="practice-label" x="394" y="490">REFLECT</text>
  </g>
  <g class="practice-group">
    <use href="#pair-link" x="191" y="582"/>
    <use href="#chevron" class="practice-rust" x="115" y="606"/>
    <text class="practice-label" x="192" y="666">STUDY</text>
    <use href="#chevron" class="practice-olive" x="319" y="606"/>
    <text class="practice-label" x="386" y="671">MEMORIZE</text>
  </g>
  <g class="practice-group">
    <use href="#pair-link" x="191" y="764"/>
    <use href="#chevron" class="practice-rust" x="115" y="788"/>
    <text class="practice-label" x="193" y="848">CONNECT</text>
    <use href="#chevron" class="practice-olive" x="319" y="788"/>
    <text class="practice-label" x="399" y="848">LEARN</text>
  </g>

  <!-- Practices: God's work through me -->
  <g class="practice-group">
    <use href="#pair-link" x="812" y="404"/>
    <use href="#chevron" class="practice-rust" x="735" y="428"/>
    <text class="practice-label" x="817" y="490">FAST</text>
    <use href="#chevron" class="practice-olive" x="940" y="428"/>
    <text class="practice-label" x="1020" y="492">INTERCEDE</text>
  </g>
  <g class="practice-group">
    <use href="#pair-link" x="812" y="586"/>
    <use href="#chevron" class="practice-rust" x="735" y="610"/>
    <text class="practice-label" x="808" y="683">TEACH</text>
    <use href="#chevron" class="practice-olive" x="940" y="610"/>
    <text class="practice-label" x="1011" y="679">PROCLAIM</text>
  </g>
  <g class="practice-group">
    <use href="#pair-link" x="812" y="748"/>
    <use href="#chevron" class="practice-rust" x="735" y="772"/>
    <text class="practice-label" x="808" y="841">GIVE</text>
    <use href="#chevron" class="practice-olive" x="940" y="772"/>
    <text class="practice-label" x="1025" y="839">SERVE</text>
  </g>
</svg>
</body>
</html>
```